Flyer-Design für Baumfällungen und -pflege
Zielgruppe
Wir bieten Baumpflege und Baumfällungen an. Das Design sollte hochwertig, schlicht und sympathisch sein. Zielgruppe sind Eigentümer von Bäumen jeglichen Alters.
Aufgabenstellung
Homepage: www.astwerkmeister.com
Logo bitte vorerst von der Homepage verwenden. Ich habe die Datei noch nicht, kann sie aber besorgen, Bilder kann ich auch noch liefern bei Bedarf. Text kann auch, am Besten in abgespeckter Form oder nur die Überschriften z.B. der Leistungen, von Homepage verwendet werden.
Flyer und Design sollen sein:
- sympathisch
- vertrauensvoll
- professionell
- übersichtlich
- handlich

```html
<!DOCTYPE html>
<html lang="de">
<head>
<meta charset="utf-8">
<title>AstwerkMeister Flyer</title>
<link href="https://fonts.googleapis.com/css2?family=Roboto:wght@300;400;700;900&display=swap" rel="stylesheet">
<style>
:root{
  --orange:#f39220;
  --dark:#2b2b2b;
  --ink:#2a2a2a;
  --white:#ffffff;
  --wood:#b89a86;
  --wood-dark:#8e6a5c;
  --wood-light:#dccabd;
  --snow:#dfe7f0;
}
*{box-sizing:border-box;margin:0;padding:0}
html,body{width:880px;height:1200px;overflow:hidden;background:#fff;font-family:"Roboto",Arial,sans-serif;color:var(--ink)}
.card{position:absolute;left:76px;width:728px;height:520px;background:var(--white);overflow:hidden}
.card--front{top:20px}
.card--back{top:628px}
.band{position:absolute;left:0;width:100%;height:48px;background:var(--dark)}
.band--top{top:0}
.band--bottom{bottom:0}
.portrait{position:absolute;width:150px;height:150px;border-radius:50%;background:radial-gradient(circle at 50% 35%,#e8c6a8 0 18%,#6fa0d8 19% 55%,#c9d64a 56% 75%,#d9442e 76%);border:3px solid #fff}

/* front */
.forest{position:absolute;left:0;top:48px;width:364px;height:424px;background:linear-gradient(90deg,#fff 0%,rgba(255,255,255,.4) 35%,rgba(255,255,255,0) 60%),linear-gradient(180deg,#a9c6e6 0%,var(--snow) 45%,#8a8f94 75%,#eef2f6 100%)}
.front-portrait{left:22px;top:140px}
.greeting{position:absolute;left:22px;top:302px;color:var(--orange);font-weight:700;font-size:15.5px;line-height:19px}
.contact{position:absolute;left:22px;top:346px;font-weight:300;font-size:15px;line-height:18.5px;color:var(--ink)}
.contact span{display:inline-block;width:38px}
.wood{position:absolute;left:364px;top:48px;width:364px;height:424px;background:linear-gradient(160deg,#5c7a45 0%,#c7a293 12%,var(--wood) 40%,#a88270 70%,var(--wood-dark) 100%)}
.wood-curve{position:absolute;left:364px;top:48px}
.headline{position:absolute;left:381px;top:212px;color:#fff;font-weight:900;font-size:31px;line-height:33px;text-shadow:1px 1px 2px rgba(0,0,0,.35)}
.headline em{font-style:normal;color:var(--orange)}
.tagline{position:absolute;left:381px;top:420px;color:#fff;font-weight:700;font-size:16.5px;line-height:20px}
.brand-box{position:absolute;left:589px;top:0;width:139px;height:74px;background:#fff;border:1px solid var(--orange);display:flex;align-items:center;justify-content:center;gap:6px}
.brand-box .dot{width:12px;height:12px;border-radius:50%;background:var(--orange)}
.brand-name{font-weight:700;font-size:13px;color:var(--dark)}

/* back */
.services-title{position:absolute;left:0;width:728px;top:13px;padding-left:390px;color:var(--orange);font-weight:700;font-size:17px;text-align:left}
.back-wood{position:absolute;left:190px;top:48px;width:230px;height:424px;
  background:linear-gradient(180deg,var(--wood-light) 0%,#d2b9aa 55%,#c9a899 100%);
  -webkit-mask-image:linear-gradient(90deg,transparent 0%,#000 28%,#000 55%,transparent 100%);
  mask-image:linear-gradient(90deg,transparent 0%,#000 28%,#000 55%,transparent 100%)}
.back-portrait{left:22px;top:33px}
.about{position:absolute;left:22px;top:219px;width:220px;font-size:10px;line-height:12.4px;font-weight:300}
.about h3{color:var(--orange);font-weight:700;font-size:10.5px;line-height:12.4px}
.about p+h3{margin-top:12px}
.services{position:absolute;left:374px;top:63px;display:grid;grid-template-columns:repeat(3,90px);column-gap:25px;row-gap:0}
.service{height:140px;text-align:center}
.service-img{width:90px;height:90px;border-radius:50%;border:2px solid var(--orange);background:radial-gradient(circle,#fff 0 20%,#fbe1c3 21% 50%,#cfe3b4 51%)}
.service-label{margin-top:9px;color:var(--orange);font-weight:700;font-size:8.5px;line-height:10.5px}
.footer-line{position:absolute;bottom:13px;color:#e8e8e8;font-weight:300;font-size:15.5px}
.footer-line--left{left:17px}
.footer-line--right{right:17px}
</style>
</head>
<body>

<section class="card card--front">
  <div class="band band--top"></div>
  <div class="forest" role="img" aria-label="Foto: verschneiter Nadelwald im Winter"></div>
  <div class="portrait front-portrait" role="img" aria-label="Porträtfoto des Baumpflegers mit Schutzhelm"></div>
  <p class="greeting">Ich freue mich, von<br>Ihnen zu hören!</p>
  <p class="contact">Jonas Reinhardt<br>Lindenweg 12<br>79999 Tannenbach<br><span>tel.:</span>0151 000 123 45<br>mail: j.reinhardt@waldpost.de<br>web: www.astwerkmeister.com</p>

  <div class="wood" role="img" aria-label="Foto: Schnittfläche eines gefällten Baumstamms"></div>
  <svg class="wood-curve" width="364" height="424" viewBox="0 0 364 424" aria-hidden="true">
    <path d="M0 424 L0 340 C120 355 300 330 364 190 L364 424 Z" fill="var(--orange)"/>
  </svg>
  <h1 class="headline"><em>Hallo</em> und<br>herzlich<br>willkommen<br>bei <em>AstwerkMeister!</em></h1>
  <p class="tagline">Ihr Profi für Baumpflege<br>im Hochschwarzwald</p>
  <div class="brand-box"><span class="dot"></span><span class="brand-name">AstwerkMeister</span></div>
  <div class="band band--bottom"></div>
</section>

<section class="card card--back">
  <div class="band band--top"></div>
  <h2 class="services-title">Unsere Leistungen</h2>
  <div class="back-wood" role="img" aria-label="Foto: Holzmaserung einer Stammschnittfläche, verblasst"></div>
  <div class="portrait back-portrait" role="img" aria-label="Porträtfoto des Baumpflegers mit Schutzhelm"></div>
  <div class="about">
    <h3>Hallo</h3>
    <p>Ich bin Jonas Reinhardt und lebe mit meiner Familie in Tannenbach. Zusammen mit meinem Team biete ich als „AstwerkMeister“ alle Arbeiten rund um den Baum an. – Vom Baum pflanzen über Baumpflege bis hin zur Fällung. Dies auch an schwer zugänglichen Standorten.</p>
    <h3>Wie ich zur Baumpflege gekommen bin</h3>
    <p>Bäume faszinieren mich schon seit meiner Kindheit. Sie laden ein zum Klettern, zum Verweilen oder spenden Schutz vor Sonne, Regen und Wind. Sie wurden gepflanzt von Mutter Natur oder durch Menschenhand, von unseren Vätern und Großvätern für uns oder von uns für unsere Kinder und Enkel. Geduldig trotzen sie den Belastungen, denen sie im Laufe ihres langen Lebens ausgesetzt sind. Für mich ist die Arbeit mit diesen Bäumen und mit Holz eine der schönsten Tätigkeiten, die es gibt.</p>
  </div>
  <div class="services">
    <div class="service"><div class="service-img" role="img" aria-label="Illustration: Baumkontrolle am Stamm"></div><p class="service-label">Baumkontrolle<br>nach FLL</p></div>
    <div class="service"><div class="service-img" role="img" aria-label="Illustration: Pflege eines Jungbaums von der Leiter"></div><p class="service-label">Jungbaumpflege</p></div>
    <div class="service"><div class="service-img" role="img" aria-label="Illustration: Kletterer in der Baumkrone"></div><p class="service-label">Kronenpflege</p></div>
    <div class="service"><div class="service-img" role="img" aria-label="Illustration: Hubarbeitsbühne an einem Baum"></div><p class="service-label">Totholz-<br>beseitigung</p></div>
    <div class="service"><div class="service-img" role="img" aria-label="Illustration: Seilsicherung in einer Baumkrone"></div><p class="service-label">Kronensicherung</p></div>
    <div class="service"><div class="service-img" role="img" aria-label="Illustration: Lkw auf einer Straße zwischen Bäumen"></div><p class="service-label">Herstellung<br>Lichtraumprofils</p></div>
    <div class="service"><div class="service-img" role="img" aria-label="Illustration: Fällung mit Motorsäge"></div><p class="service-label">Baumfällungen</p></div>
    <div class="service"><div class="service-img" role="img" aria-label="Illustration: Häcksler mit Arbeiter"></div><p class="service-label">Abtransport &amp;<br>Häckseln</p></div>
    <div class="service"><div class="service-img" role="img" aria-label="Illustration: Stubbenfräse am Wurzelstock"></div><p class="service-label">Entfernung von<br>Wurzelstöcken</p></div>
  </div>
  <div class="band band--bottom"></div>
  <p class="footer-line footer-line--left">professionell – aus einer Hand</p>
  <p class="footer-line footer-line--right">professionell – aus einer Hand</p>
</section>

</body>
</html>
```